Unique Business Card Design

Unique Business Card design for our orthotic and prosthetic company. Our logo is on our website, color is light blue. Unique shape (artificial leg shaped, vertical, etc..) preferred. Logo, business name, individual name and basic demographics needed.

Industry/Entity Type

Business

Contact Information for Business Card

Logo, Industry, Phone # Logo, "Prosthetic & Orthotic Services" Place to add individual name and contact info

Colors
cee9f5

Requirements
Must have
• The icon must be there, placement of "Prosthetic & Orthotic Services" can be moved
Nice to have
• Like the mix of light blue, and a little darker blue. One design included the icons from my website which was a nice touch

```html
<!DOCTYPE html>
<html lang="en">
<head>
<meta charset="utf-8">
<title>Limbwell Inc. business card</title>
<link href="https://fonts.googleapis.com/css2?family=Arimo:wght@400;700&display=swap" rel="stylesheet">
<style>
  :root {
    --backdrop: #3a322d;
    --card: #121314;
    --card-edge: #1c1d1f;
    --blue: #2f7fd0;
    --blue-light: #cee9f5;
    --silver: #c9c9c9;
    --silver-dim: #8e8e8e;
    --gloss: #2a2b2d;
    --text: #e8e8e8;
  }
  * { margin: 0; padding: 0; box-sizing: border-box; }
  html, body { width: 1200px; height: 864px; overflow: hidden; }
  body {
    background: var(--backdrop);
    font-family: "Arimo", Arial, sans-serif;
    position: relative;
  }
  .card {
    position: absolute;
    width: 560px;
    height: 320px;
    background: var(--card);
    border: 1px solid var(--card-edge);
    box-shadow: 0 10px 24px rgba(0,0,0,.45);
  }
  /* Back of card */
  .card-back { left: 50px; top: 80px; }
  .card-back .mark {
    position: absolute; left: 110px; top: 78px;
    width: 84px; height: 84px; border-radius: 50%;
    background: radial-gradient(circle at 35% 35%, #e6e6e6, var(--silver-dim));
  }
  .card-back .brand {
    position: absolute; left: 212px; top: 100px;
    font-size: 30px; font-weight: 700; letter-spacing: .5px;
    color: var(--gloss);
  }
  .card-back .brand-rule {
    position: absolute; left: 212px; top: 138px; width: 250px; height: 2px;
    background: var(--gloss);
  }
  .card-back .tagline {
    position: absolute; left: 212px; top: 146px;
    font-size: 13px; color: var(--gloss);
  }
  .card-back .footer {
    position: absolute; left: 40px; right: 40px; top: 248px;
    display: flex; align-items: center; gap: 16px;
  }
  .card-back .footer .rule { flex: 1; height: 1px; background: var(--silver-dim); }
  .card-back .footer .web { font-size: 13px; color: var(--silver); }

  /* Front of card */
  .card-front { left: 590px; top: 454px; }
  .card-front .logo {
    position: absolute; right: 30px; top: 34px;
    display: flex; align-items: center; gap: 14px;
  }
  .card-front .logo .mark {
    width: 64px; height: 64px; border-radius: 50%; background: var(--blue);
  }
  .card-front .logo .brand {
    font-size: 24px; font-weight: 700; color: var(--blue);
    border-bottom: 2px solid var(--blue); padding-bottom: 3px;
  }
  .card-front .logo .tagline {
    font-size: 11px; color: var(--blue); margin-top: 4px;
  }
  .card-front .person {
    position: absolute; left: 30px; top: 40px;
    font-size: 20px; color: var(--blue);
  }
  .card-front .person .cred { font-size: 13px; }
  .card-front .divider {
    position: absolute; left: 30px; right: 30px; top: 118px;
    height: 1px; background: var(--silver-dim);
  }
  .card-front .contacts {
    position: absolute; left: 30px; top: 134px;
    list-style: none; font-size: 13px; color: var(--text); line-height: 21px;
  }
  .card-front .contacts li { display: flex; align-items: center; gap: 9px; }
  .card-front .contacts svg { width: 13px; height: 13px; fill: var(--blue); }
  .card-front .address {
    position: absolute; right: 30px; bottom: 28px;
    text-align: right; font-size: 15px; color: var(--text); line-height: 21px;
  }
</style>
</head>
<body>

<section class="card card-back" aria-label="Card back">
  <div class="mark"></div>
  <div class="brand">LIMBWELL INC.</div>
  <div class="brand-rule"></div>
  <div class="tagline">Prosthetic &amp; Orthotic Services</div>
  <div class="footer">
    <span class="rule"></span>
    <span class="web">www.limbwellinc.com</span>
    <span class="rule"></span>
  </div>
</section>

<section class="card card-front" aria-label="Card front">
  <div class="person">Miriam Kessler, <span class="cred">CO LPO</span></div>
  <div class="logo">
    <div class="mark"></div>
    <div>
      <div class="brand">LIMBWELL INC.</div>
      <div class="tagline">Prosthetic &amp; Orthotic Services</div>
    </div>
  </div>
  <div class="divider"></div>
  <ul class="contacts">
    <li><svg viewBox="0 0 16 16"><path d="M3 1l3 3-2 2c1 2 3 4 5 5l2-2 3 3-2 3C6 15 1 10 1 3z"/></svg>555.201.4400</li>
    <li><svg viewBox="0 0 16 16"><rect x="4" y="0" width="8" height="16" rx="1.5"/></svg>555.201.4419</li>
    <li><svg viewBox="0 0 16 16"><rect x="1" y="6" width="14" height="9" rx="1"/><rect x="4" y="1" width="8" height="5"/></svg>555-3817260</li>
    <li><svg viewBox="0 0 16 16"><path d="M1 3h14v10H1z M1 3l7 6 7-6" stroke="#121314" stroke-width="1"/></svg>mkessler@limbwellinc.com</li>
  </ul>
  <div class="address">
    820 Harbor Ave.<br>
    Lakeview, NY 10990<br>
    www.limbwellinc.com
  </div>
</section>

</body>
</html>
```